We (R. T. Galvin & Partners, Inc.) are an executive Search firm based in Los Angeles that is exclusively focused in the Med Tech and Health Tech arenas.   I need a logo to communicate that we are a high end search firm, but also that we are focused in the medicine and science arenas called health tech and med tech.  Many of our clients have robotics and artificial intelligence type products, so it is very technology forward.  I tend to gravitate towards clean, sharp aesthetic as opposed to something that is really over the top.
Attached are files with my logo in two different layouts.  In addition to the letterhead and envelope, I also will need an electronic letterhead in Microsoft Word.  I tend to
I look forward to seeing the designs and just let me know if you have any questions.
Dale

```html
<!DOCTYPE html>
<html lang="en">
<head>
<meta charset="utf-8">
<title>R. T. Galvin &amp; Partners — Stationery Set</title>
<link rel="stylesheet" href="https://fonts.googleapis.com/css2?family=Montserrat:wght@300;400;600&family=Arimo:wght@400&display=swap">
<style>
:root{
  --bg:#a9a9a9;
  --ink:#060606;
  --blue:#4fa3dc;
  --paper:#ffffff;
  --paper-shade:#eeeeef;
  --grey-text:#8a8a8a;
  --body-text:#9a9a9a;
}
*{box-sizing:border-box;margin:0;padding:0}
html,body{width:1200px;height:1190px;overflow:hidden;background:var(--bg)}
body{position:relative;font-family:'Montserrat',sans-serif;color:var(--ink)}
.sheet{position:absolute;overflow:hidden;box-shadow:1px 1px 3px rgba(0,0,0,.35);
  background:linear-gradient(180deg,var(--paper-shade) 0%,var(--paper) 70%)}
.abs{position:absolute}

/* plain header band: black bar with a straight blue rule beneath */
.header-band{position:absolute;left:0;top:0;width:100%;background:var(--ink)}
.header-band::after{content:"";position:absolute;left:0;right:0;background:var(--blue)}
.band-lg{height:34px}
.band-lg::after{top:40px;height:5px}
.band-md{height:24px}
.band-md::after{top:28px;height:4px}
.band-sm{height:16px}
.band-sm::after{top:19px;height:3px}

.brand{position:absolute;font-weight:600;color:var(--ink);white-space:nowrap;line-height:1}
.brand .name{display:block;letter-spacing:-.3px}
.brand .sub{display:block;font-weight:600}
.brand.light{color:#fff}
.brand-dot{position:absolute;border-radius:50%;background:var(--blue)}

/* letterhead */
.letterhead{left:40px;top:50px;width:556px;height:786px}
.letterhead .brand{left:36px;top:93px}
.letterhead .brand .name{font-size:21px}
.letterhead .brand .sub{font-size:8.2px;letter-spacing:2.4px;margin-top:4px}
.to-label{left:57px;top:181px;font-size:10px;letter-spacing:1px}
.recipient{left:57px;top:197px;font-size:9.5px;color:var(--blue)}
.address-line{left:57px;font-size:7.5px;font-weight:300;color:var(--grey-text)}
.date{right:56px;top:181px;font-size:7.5px;color:var(--grey-text);font-weight:300}
.letter-body{left:57px;top:283px;width:444px;font-size:7.9px;line-height:9.8px;font-weight:300;color:var(--body-text);text-align:justify}
.letter-body p{margin-bottom:10px}
.signature-mark{left:57px;top:555px;width:100px;height:22px;background:linear-gradient(90deg,#d8d8d8,#efefef);border-radius:2px}
.signer{left:56px;top:590px;font-size:8.5px;font-weight:400}
.signer-role{left:55px;top:601px;font-size:7.5px;color:var(--grey-text);font-weight:300}
.footer-address{left:0;width:556px;text-align:center;top:732px;font-family:'Arimo',sans-serif;font-size:10px}
.footer-rule{left:125px;top:748px;width:306px;height:1px;background:#666}
.footer-contacts{left:0;width:556px;top:754px;display:flex;justify-content:center;gap:9px;align-items:center;font-family:'Arimo',sans-serif;font-size:10px}
.footer-contacts span{display:flex;align-items:center;gap:5px}
.footer-contacts svg{fill:var(--blue)}

/* folder cover */
.folder-cover{left:622px;top:50px;width:538px;height:380px}
.cover-back{left:0;top:0;width:269px;height:380px;background:var(--ink)}
.cover-front{left:269px;top:0;width:269px;height:380px;overflow:hidden;background:linear-gradient(160deg,#e2e2e4 0%,#ffffff 55%)}
.cover-front .brand{left:107px;top:178px}
.cover-front .brand .name{font-size:15.5px}
.cover-front .brand .sub{font-size:6px;letter-spacing:1.8px;margin-top:3px}
.cover-contact{top:350px;font-family:'Arimo',sans-serif;font-size:3.6px;line-height:4.6px;white-space:nowrap}
.cover-split{top:349px;width:.6px;height:15px;background:#777}

/* folder open */
.folder-open{left:623px;top:458px;width:535px;height:378px;background:#fff}
.inner-left{left:0;top:0;width:268px;height:378px;background:linear-gradient(90deg,#fafafa 0%,#e3e3e5 100%)}
.inner-right{left:268px;top:0;width:267px;height:378px;background:linear-gradient(90deg,#bdbdbd 0%,#f2f2f2 8%,#fff 40%)}
.mini-letter{left:281px;top:18px;width:241px;height:230px;background:linear-gradient(180deg,#ededee,#fff 70%);overflow:hidden}
.mini-letter .brand{left:16px;top:42px}
.mini-letter .brand .name{font-size:9px}
.mini-letter .brand .sub{font-size:3.6px;letter-spacing:1px;margin-top:1.5px}
.mini{font-size:3.2px;line-height:4px;color:var(--grey-text);font-weight:300;white-space:nowrap}
.mini-body{left:25px;top:124px;width:194px;font-size:2.7px;line-height:3.6px;color:#9d9d9d;text-align:justify;font-weight:300}
.mini-body p{margin-bottom:3px}
.pockets{left:0;top:0}

/* envelopes */
.envelope-front{left:40px;top:864px;width:548px;height:238px}
.envelope-front .brand{left:72px;top:46px}
.envelope-front .brand .name{font-size:14.5px}
.envelope-front .brand .sub{font-size:5.8px;letter-spacing:1.6px;margin-top:2px}
.return-address{left:72px;top:70px;font-family:'Arimo',sans-serif;font-size:8px;line-height:10px}
.envelope-back{left:625px;top:870px;width:527px;height:228px;background:linear-gradient(180deg,#ececed,#fff 60%)}
.envelope-back .brand{left:241px;top:27px}
.envelope-back .brand .name{font-size:14px}
.envelope-back .brand .sub{font-size:5.6px;letter-spacing:1.6px;margin-top:2px}
.flap{position:absolute;left:0;top:0;display:block}
</style>
</head>
<body>

<!-- Letterhead -->
<section class="sheet letterhead">
  <div class="header-band band-lg"></div>
  <span class="brand-dot" style="left:100px;top:56px;width:18px;height:18px"></span>
  <div class="brand"><span class="name">R. T. GALVIN</span><span class="sub">&amp; PARTNERS, INC.</span></div>

  <div class="abs to-label">TO</div>
  <div class="abs date">Friday, 01/01/2018</div>
  <div class="abs recipient">Ava Renfield</div>
  <div class="abs address-line" style="top:213px">Human Resources</div>
  <div class="abs address-line" style="top:225px">Larkspur Medical Co.</div>
  <div class="abs address-line" style="top:237px">240 Orchard Lane, Pasadena</div>
  <div class="abs address-line" style="top:250px">CA 91101 USA</div>

  <div class="abs letter-body">
    <p>Lorem ipsum dolor sit amet, consectetuer adipiscing elit, sed diam nonummy nibh euismod tincidunt ut laoreet dolore magna aliquam erat volutpat. Ut wisi enim ad minim veniam, quis nostrud exerci tationmcorper suscipit lobortis nisl ut aliquip ex ea commodo consequat. Duis autem vel eum iriure dolor in hendrerit in vulputate velit esse molestie consequat, vel illum dolore eu feugiat nulla facilisis at vero eros et accumsan et iusto odio dignissim qui blandit praesent luptatum zzril delenit augue duis dolore te feugait nulla facilisi.</p>
    <p>Nam liber tempor cum soluta nobis eleifend option congue nihil imprdiet doming id quod mazim placerat facer possim assum. Typi non habent claritatem insitam;</p>
    <p>Est usus legentis in iis qui facit eorum claritatem.</p>
    <p>Investigationes demonstraverunt lectores legere me lius quod ii legunt saepius. Claritas est etiam processus dynamicus, qui sequitur mutationem consuetudium lectorum. Mirum est notare quam littera gothica, quam nunc putamus parum claram, anteposuerit litterarum formas humanitatis per seacula quarta decima et quinta decima. Eodem modo typi, qui nunc nobis videntur parum clari, fiant sollemnes in futurum.</p>
    <p>consectetuer adipiscing elit, sed diam nonummy nibh euismod tincidunt ut laoreet dolore magna aliquam erat volutpat. Ut wisi enim ad minim veniam, quis nostrud exerci tation ullamcorper suscipit lobortis nisl ut aliquip ex ea commodo consequat. Duis autem vel eum iriure dolor in hendrerit in vulputate velit esse molestie consequat, vel illum dolore eu feugiat nulla facilisis at vero eros et accumsan et iusto odio dignissim qui blandit praesent luptatum zzril delenit augue duis dolore te feugait nulla facilisi.</p>
    <p>Nam liber tempor cum soluta nobis eleifend option congue nihil imperdiet .</p>
  </div>

  <div class="abs signature-mark" role="img" aria-label="Handwritten signature of Owen Hartley"></div>
  <div class="abs signer">Owen Hartley</div>
  <div class="abs signer-role">Managing Director</div>

  <div class="abs footer-address">Your address, city, state, ZIP 0000</div>
  <div class="abs footer-rule"></div>
  <div class="abs footer-contacts">
    <span><svg width="8" height="8" viewBox="0 0 10 10"><path d="M2 0 L4 2.5 L3 3.6 Q4.2 5.8 6.4 7 L7.5 6 L10 8 L8.6 9.8 Q3.5 9 0.2 1.4 Z"/></svg>555-014-2100</span>
    <span><svg width="9" height="7" viewBox="0 0 10 7"><path d="M0 0 H10 L5 3.6 Z M0 1.2 L5 4.8 L10 1.2 V7 H0 Z"/></svg>contact@galvinpartners.com</span>
    <span><svg width="8" height="8" viewBox="0 0 10 10"><circle cx="5" cy="5" r="4.3" fill="none" stroke="var(--blue)" stroke-width="1.3"/><path d="M0.7 5 H9.3 M5 0.7 V9.3" stroke="var(--blue)" stroke-width="1"/></svg>www.galvinpartners.com</span>
  </div>
</section>

<!-- Presentation folder, outside -->
<section class="sheet folder-cover">
  <div class="abs cover-back"></div>
  <div class="abs cover-front">
    <div class="header-band band-md"></div>
    <span class="brand-dot" style="left:143px;top:180px;width:14px;height:14px;display:none"></span>
    <span class="brand-dot" style="left:88px;top:180px;width:13px;height:13px"></span>
    <div class="brand"><span class="name">R. T. GALVIN</span><span class="sub">&amp; PARTNERS, INC.</span></div>
    <div class="abs cover-contact" style="left:122px;width:60px;text-align:right">Your address, city<br>state, ZIP 0000</div>
    <div class="abs cover-split" style="left:185px"></div>
    <div class="abs cover-contact" style="left:189px">555-014-2100<br>contact@galvinpartners.com<br>www.galvinpartners.com</div>
  </div>
</section>

<!-- Presentation folder, inside -->
<section class="sheet folder-open">
  <div class="abs inner-left"></div>
  <div class="abs inner-right"></div>
  <div class="abs mini-letter">
    <div class="header-band band-sm"></div>
    <span class="brand-dot" style="left:45px;top:26px;width:8px;height:8px"></span>
    <div class="brand"><span class="name">R. T. GALVIN</span><span class="sub">&amp; PARTNERS, INC.</span></div>
    <div class="abs mini" style="left:25px;top:77px;color:var(--ink);font-size:4px">TO</div>
    <div class="abs mini" style="right:22px;top:77px">Friday, 01/01/2018</div>
    <div class="abs mini" style="left:25px;top:85px;color:var(--blue)">Ava Renfield</div>
    <div class="abs mini" style="left:25px;top:91px">Human Resources<br>Larkspur Medical Co.<br>240 Orchard Lane, Pasadena<br>CA 91101 USA</div>
    <div class="abs mini-body">
      <p>Thank you for your time last week. We are pleased to share the shortlist of candidates for your review.</p>
      <p>Each profile includes career notes and references.</p>
      <p>We welcome your feedback.</p>
      <p>Interviews can begin next month at your office or by video, whichever suits your team best.</p>
      <p>Kind regards from all of us.</p>
    </div>
  </div>
  <svg class="abs pockets" width="535" height="378" viewBox="0 0 535 378" aria-hidden="true">
    <path fill="var(--ink)" d="M0 244 H240 Q252 244 254 258 L267 378 H0 Z"/>
    <path fill="var(--ink)" d="M535 244 H296 Q287 244 285 256 L268 378 H535 Z"/>
  </svg>
</section>

<!-- Envelope, front -->
<section class="sheet envelope-front">
  <div class="header-band band-md"></div>
  <span class="brand-dot" style="left:40px;top:46px;width:18px;height:18px"></span>
  <div class="brand"><span class="name">R. T. GALVIN</span><span class="sub">&amp; PARTNERS, INC.</span></div>
  <div class="abs return-address">Your address, city<br>state, ZIP 0000</div>
</section>

<!-- Envelope, back -->
<section class="sheet envelope-back">
  <svg class="flap" width="527" height="64" viewBox="0 0 527 64" aria-hidden="true">
    <path fill="var(--ink)" d="M0 0 H527 L511 48 Q506 63 490 63 H37 Q21 63 16 48 Z"/>
  </svg>
  <span class="brand-dot" style="left:213px;top:28px;width:14px;height:14px"></span>
  <div class="brand light"><span class="name">R. T. GALVIN</span><span class="sub">&amp; PARTNERS, INC.</span></div>
</section>

</body>
</html>
```